Plumbing & Heating company

A leaflet containing -

Company name - Larkfield Plumbing Solutions
logo
Mobile number - 07700 914062
Landline - 01632 870215
Email - Info@larkfieldplumbing.example
website - Larkfield-plumbing.example
Social media logos - insta, Facebook

services we offer

- Boiler replacements (free quote)
- General plumbing & heating
- Tap replacements
- 1st & 2nd
- New builds & Extensions
- Cylinder replcemets

```html
<!DOCTYPE html>
<html lang="en">
<head>
<meta charset="utf-8">
<title>Larkfield Plumbing Solutions – Leaflet</title>
<link rel="stylesheet" href="https://fonts.googleapis.com/css2?family=Bebas+Neue&family=Oswald:wght@500;600&family=Montserrat:wght@500&family=Roboto:wght@400&display=swap">
<style>
  :root {
    --blue: #1565b0;
    --blue-dark: #0f4f93;
    --red: #f42e3c;
    --orange: #f7731f;
    --yellow: #fbb61d;
    --ink: #3e3e3e;
    --white: #ffffff;
    --backdrop: #bdbdbd;
  }
  * { margin: 0; padding: 0; box-sizing: border-box; }
  html, body { width: 1200px; height: 2400px; overflow: hidden; background: var(--backdrop); }
  .canvas { position: relative; width: 1200px; height: 2400px; }
  .leaflet {
    position: absolute; left: 22px; top: 379px;
    width: 963px; height: 1368px;
    transform: scale(1.2); transform-origin: top left;
    background: var(--white);
    box-shadow: 0 6px 14px rgba(0,0,0,.25);
    overflow: hidden;
  }
  .leaflet-shapes { position: absolute; inset: 0; }
  .brand-mark {
    position: absolute; left: 70px; top: 52px; width: 300px;
    display: flex; align-items: center; justify-content: center; gap: 12px;
    font-family: "Oswald", sans-serif; font-weight: 600; color: var(--blue);
    text-align: center; line-height: 1;
  }
  .brand-mark .dot { width: 22px; height: 22px; border-radius: 50%; background: var(--orange); flex: none; }
  .brand-mark .name { font-size: 30px; letter-spacing: 1px; }
  .brand-mark .name small { display: block; font-size: 17px; letter-spacing: 3px; margin-top: 6px; }
  .headline {
    position: absolute; left: 28px; top: 150px;
    font-family: "Bebas Neue", sans-serif; font-size: 104px; line-height: 1;
    background: linear-gradient(90deg, var(--red), var(--orange) 60%, var(--yellow));
    -webkit-background-clip: text; background-clip: text; color: transparent;
  }
  .subhead {
    position: absolute; left: 30px; top: 238px;
    font-family: "Bebas Neue", sans-serif; font-size: 54px; line-height: 1;
    color: var(--blue); letter-spacing: .5px;
  }
  .intro {
    position: absolute; left: 34px; top: 296px; width: 370px;
    font-family: "Montserrat", sans-serif; font-weight: 500;
    font-size: 26px; line-height: 36px; color: var(--ink);
  }
  .services-title {
    position: absolute; left: 50px; top: 858px;
    font-family: "Bebas Neue", sans-serif; font-size: 56px; line-height: 60px;
    color: var(--white); letter-spacing: 1px;
  }
  .services-list {
    position: absolute; left: 34px; top: 940px; width: 425px; list-style: none;
    font-family: "Oswald", sans-serif; font-weight: 500; font-size: 27px;
    color: var(--ink); line-height: 49.4px; text-transform: uppercase;
    white-space: nowrap;
  }
  .services-list li { display: flex; align-items: center; gap: 9px; }
  .services-list li::before {
    content: ""; width: 13px; height: 13px; border-radius: 50%;
    background: linear-gradient(135deg, var(--yellow), var(--red)); flex: none;
  }
  .mobile {
    position: absolute; left: 40px; top: 1268px;
    font-family: "Oswald", sans-serif; font-weight: 500; font-size: 66px; line-height: 90px;
    color: var(--white);
  }
  .contact-list {
    position: absolute; left: 468px; top: 1248px; list-style: none;
    font-family: "Roboto", sans-serif; font-size: 24px; line-height: 30px; color: var(--white);
  }
  .contact-list li { display: flex; align-items: center; gap: 8px; }
  .contact-list svg { width: 20px; height: 20px; flex: none; }
  .social { position: absolute; right: 36px; top: 1310px; display: flex; gap: 10px; }
  .social span { width: 32px; height: 32px; border-radius: 8px; background: var(--white); }
</style>
</head>
<body>
<div class="canvas">
  <div class="leaflet">
    <svg class="leaflet-shapes" viewBox="0 0 963 1368" width="963" height="1368">
      <defs>
        <linearGradient id="warm" x1="0" y1="0" x2="1" y2="0">
          <stop offset="0" stop-color="#fbb61d"/><stop offset="1" stop-color="#f42e3c"/>
        </linearGradient>
        <linearGradient id="warm-rev" x1="0" y1="0" x2="1" y2="0">
          <stop offset="0" stop-color="#f42e3c"/><stop offset=".55" stop-color="#f7731f"/><stop offset="1" stop-color="#fbb61d"/>
        </linearGradient>
        <linearGradient id="warm-down" x1="0" y1="0" x2="0" y2="1">
          <stop offset="0" stop-color="#fbb61d"/><stop offset="1" stop-color="#f7731f"/>
        </linearGradient>
        <linearGradient id="blue-band" x1="0" y1="0" x2="1" y2="0">
          <stop offset="0" stop-color="#1a76c4"/><stop offset="1" stop-color="#0f4f93"/>
        </linearGradient>
        <linearGradient id="cupboard" x1="0" y1="0" x2="1" y2="1">
          <stop offset="0" stop-color="#e8e6e2"/><stop offset=".55" stop-color="#cfcac2"/><stop offset="1" stop-color="#8c8478"/>
        </linearGradient>
        <linearGradient id="plywood" x1="0" y1="0" x2="1" y2="1">
          <stop offset="0" stop-color="#c89c6e"/><stop offset=".5" stop-color="#dcc0a0"/><stop offset="1" stop-color="#a97a4e"/>
        </linearGradient>
        <linearGradient id="floor" x1="0" y1="0" x2="1" y2="1">
          <stop offset="0" stop-color="#a99a86"/><stop offset=".5" stop-color="#b67a52"/><stop offset="1" stop-color="#7d756c"/>
        </linearGradient>
      </defs>

      <rect x="465" y="420" width="460" height="805" fill="var(--blue)"/>
      <polygon points="418,418 738,600 963,425 963,470 738,632 418,440" fill="url(#warm-rev)"/>
      <rect x="418" y="0" width="14" height="430" fill="url(#warm-down)"/>
      <polygon points="432,0 963,0 963,410 738,585 432,425" fill="url(#cupboard)"
        role="img" aria-label="Photo of a white hot water cylinder and wall-hung boiler with copper pipework in a cupboard"/>

      <rect x="480" y="665" width="430" height="545" rx="28" fill="url(#floor)" stroke="#ffffff" stroke-width="4"
        role="img" aria-label="Photo of copper underfloor pipe runs laid between timber joists"/>

      <rect x="36" y="495" width="398" height="305" rx="32" fill="url(#plywood)" stroke="url(#warm)" stroke-width="6"
        role="img" aria-label="Photo of a combi boiler with pipework on a plywood wall"/>

      <rect x="35" y="855" width="430" height="65" fill="url(#warm-rev)"/>

      <polygon points="448,1237 963,1237 963,1368 372,1368" fill="url(#warm)"/>
      <polygon points="0,1258 452,1258 372,1368 0,1368" fill="url(#blue-band)"/>
    </svg>

    <div class="brand-mark">
      <span class="dot"></span>
      <span class="name">LARKFIELD<small>PLUMBING SOLUTIONS</small></span>
    </div>

    <h1 class="headline">LARKFIELD</h1>
    <p class="subhead">PLUMBING SOLUTIONS</p>
    <p class="intro">Larkfield Plumbing &amp; Heat-ing contractor based in Hampshire and covering Winchester and the sur-rounding areas</p>

    <h2 class="services-title">SERVICES WE OFFER</h2>
    <ul class="services-list">
      <li>Boiler replacements (free quote)</li>
      <li>General plumbing &amp; heating</li>
      <li>Tap replacements</li>
      <li>1st &amp; 2nd</li>
      <li>New builds &amp; extensions</li>
      <li>Cylinder replcemets</li>
    </ul>

    <p class="mobile">07700 914062</p>

    <ul class="contact-list">
      <li><svg viewBox="0 0 20 20"><circle cx="10" cy="10" r="9" fill="#fff"/><path d="M6.5 5.5l2 .3.6 2.2-1.2.9a7 7 0 0 0 3.2 3.2l.9-1.2 2.2.6.3 2c-.6.8-1.6 1-2.6.7A9 9 0 0 1 6 8.1c-.3-1 0-2 .5-2.6z" fill="#f7731f"/></svg>01632 870215</li>
      <li><svg viewBox="0 0 20 20"><circle cx="10" cy="10" r="9" fill="#fff"/><rect x="5" y="6.5" width="10" height="7" fill="none" stroke="#f7731f" stroke-width="1.4"/><path d="M5 6.5l5 4 5-4" fill="none" stroke="#f7731f" stroke-width="1.4"/></svg>Info@larkfieldplumbing.example</li>
      <li><svg viewBox="0 0 20 20"><circle cx="10" cy="10" r="9" fill="#fff"/><circle cx="10" cy="10" r="5.5" fill="none" stroke="#f7731f" stroke-width="1.3"/><path d="M4.5 10h11M10 4.5c-2.5 3-2.5 8 0 11M10 4.5c2.5 3 2.5 8 0 11" fill="none" stroke="#f7731f" stroke-width="1.1"/></svg>Larkfield-plumbing.example</li>
    </ul>

    <div class="social" aria-label="Social media">
      <span></span><span></span>
    </div>
  </div>
</div>
</body>
</html>
```